Young, dynamic furniture company needs a new business card design

We require a new business card design for our modern furniture company which supplies furniture and appliances to the property and development market.
Oakridge Interiors has become one of the leading furniture & appliance suppliers to the property market withing London. With over 10 years experience, we have increased our business to supply not only private landlords and managing agents, but also property developers, housing associations and local councils.
We offer not only a complete range of furniture which includes beds, wardrobes, dining sets and sofas, but also a high quality, full delivery and assembly service to help you with all our furnishing needs.

Target Market(s)

Private landlords, estate agents, letting agents, property management companies

Industry/Entity Type

Business

Contact Information for Business Card

Name,
Title,
Address,
Mobile,
Telephone,
Fax, Website, email address

Font styles to use
Sans Serif

Colors
3176b5
0555a3
85abd2
cfdeed

Requirements
Must have
• All the above information for each of our staff, along with our logo

```html
<!DOCTYPE html>
<html lang="en">
<head>
<meta charset="utf-8">
<title>Oakridge Interiors – Business Card</title>
<link href="https://fonts.googleapis.com/css2?family=Montserrat:wght@400;500;700&family=Roboto+Condensed:wght@400&display=swap" rel="stylesheet">
<style>
  :root {
    --page-bg: #e4e2df;
    --card-bg: #f7f6f4;
    --navy: #0b4a86;
    --blue: #0555a3;
    --blue-mid: #3176b5;
    --ink: #1f1d1e;
    --charcoal: #3a3839;
    --band: #201d1e;
    --rule: #6e6b6b;
  }
  * { margin: 0; padding: 0; box-sizing: border-box; }
  html, body {
    width: 1200px; height: 970px; overflow: hidden;
    background: var(--page-bg);
  }
  .card {
    position: absolute; left: 80px; top: 189px;
    width: 1040px; height: 592px;
    background: var(--card-bg);
    overflow: hidden;
    box-shadow: 0 10px 30px rgba(0,0,0,.18);
    font-family: "Montserrat", sans-serif;
    color: var(--ink);
  }
  .card__waves { position: absolute; left: 0; top: 0; width: 1040px; height: 592px; }
  .brand {
    position: absolute; left: 40px; top: 270px; width: 470px;
    text-align: center;
    font-family: "Roboto Condensed", sans-serif;
    color: var(--charcoal);
  }
  .brand__row { display: flex; align-items: center; justify-content: center; gap: 14px; }
  .brand__square { width: 26px; height: 26px; background: var(--blue-mid); }
  .brand__name { font-size: 40px; font-weight: 400; letter-spacing: .5px; line-height: 1; }
  .brand__tagline { margin-top: 12px; font-size: 22px; letter-spacing: .3px; }
  .divider {
    position: absolute; left: 510px; top: 100px;
    width: 1px; height: 330px; background: var(--rule);
  }
  .contact { position: absolute; left: 565px; top: 100px; }
  .contact__name { font-size: 35px; font-weight: 700; color: var(--navy); line-height: 1; letter-spacing: .3px; }
  .contact__title { font-size: 26px; font-weight: 500; line-height: 1.1; }
  .contact__address { margin-top: 30px; font-size: 26px; line-height: 37px; font-weight: 500; }
  .contact__list { list-style: none; margin-top: 10px; }
  .contact__item { display: flex; align-items: center; height: 37px; font-size: 27px; font-weight: 500; }
  .contact__icon {
    width: 32px; height: 32px; margin-right: 14px;
    background: var(--navy); display: flex; align-items: center; justify-content: center;
  }
  .contact__icon svg { width: 20px; height: 20px; }
</style>
</head>
<body>
  <div class="card">
    <svg class="card__waves" viewBox="0 0 1040 592" aria-hidden="true">
      <path fill="var(--blue)" d="M100,497 C400,470 800,468 1040,500 L1040,548 C850,505 500,482 100,497 Z"/>
      <path fill="var(--band)" d="M0,518 C300,490 700,495 1040,562 L1040,592 L0,592 Z"/>
    </svg>

    <div class="brand">
      <div class="brand__row">
        <span class="brand__square"></span>
        <span class="brand__name">OAKRIDGE INTERIORS</span>
      </div>
      <div class="brand__tagline">TRADE FURNITURE SOLUTIONS</div>
    </div>

    <div class="divider"></div>

    <div class="contact">
      <div class="contact__name">DANIEL HAYES</div>
      <div class="contact__title">Manager</div>
      <div class="contact__address">Your Address,2nd Ste<br>Brookfield, Texas 1234, USA</div>
      <ul class="contact__list">
        <li class="contact__item">
          <span class="contact__icon"><svg viewBox="0 0 20 20"><path fill="#fff" d="M5 2l3 4-2 2c1 3 3 5 6 6l2-2 4 3-2 3C9 18 2 11 2 4z"/></svg></span>
          123 456 7890
        </li>
        <li class="contact__item">
          <span class="contact__icon"><svg viewBox="0 0 20 20"><rect x="5" y="2" width="10" height="5" fill="#fff"/><rect x="2" y="8" width="16" height="7" fill="#fff"/><rect x="5" y="13" width="10" height="5" fill="#fff" stroke="var(--navy)" stroke-width="1"/></svg></span>
          123 456 7890
        </li>
        <li class="contact__item">
          <span class="contact__icon"><svg viewBox="0 0 20 20"><rect x="6" y="2" width="8" height="16" rx="1.5" fill="none" stroke="#fff" stroke-width="1.6"/><rect x="8" y="4" width="4" height="5" fill="#fff"/><circle cx="10" cy="14" r="1.2" fill="#fff"/></svg></span>
          123 456 7890
        </li>
        <li class="contact__item">
          <span class="contact__icon"><svg viewBox="0 0 20 20"><rect x="2" y="5" width="16" height="11" fill="none" stroke="#fff" stroke-width="1.6"/><path d="M2 5l8 6 8-6" fill="none" stroke="#fff" stroke-width="1.6"/></svg></span>
          your@yourcompany.com
        </li>
      </ul>
    </div>
  </div>
</body>
</html>
```